Design my site www.brieflyledger.com

So here is what I am thinking in terms of design:

https://plenvo.com

https://www.skyluxair.com

http://kalvex.com/harbor-plaza-tower/

I want the theme to be white and blue (royal blue). I attached a paint picture of what I would like the site to look like in terms of placing the text. Generally, what I like about the sites above is that they are simple, you can navigate easily and have some kind of idea of what's going on by looking at the center (picture and motto). Let's establish a clear understanding of how the functional part of the site would look like. Please see the picture attached.

I want to keep it simple: On top would be the Name 'BRIEFLY ledger", somewhere to the right on top on the page would be 'Sign in" button.

In the center would be a picture (maybe a video) with the Motto (on top of it all in capital) OBSERVE NAVIGATE DECIDE and below would be the "sign up now"

Below the picture (like on kalvex.com site) or to the left on top of the page would be "About Us', "Press" "Contact Us' buttons.

Then once the user gets to his page his got 3 tabs " Press Headlines", "Events", " Briefings".

we would keep the same format I only have on the site, but separate for every Tab.

I do not want the user to get distracted. I also want him to be able to access the page though mobile phone and be able to get automatic updates just like Zorvan Pings without having to sign in daily.

The landing page must be minimalist yet with business/corporate feel where users can navigate easily and a "what you see is what you get" approach. You want an image or video (personally I prefer the video.. it does capture the users attention instantly, as long as it is an interesting video), with your taglines in it.

Sections available to public: About Us, Contact Us, Landing Page with Signup Option

Private: Public Sections + User Account Page, Tabs for (Events, Press Headlines, Briefings)

Target Market(s)

PR/media monitoring/diplomatic community

Coding

Coded - Design and coding required

Number of Pages Required

1 page

Font styles to use
Serif
Sans Serif

Colors
0255a3
ec1f27

Requirements
Must have
• a simple landing page, that is user friendly.
Nice to have
• a video with the explanation of how to navigate the site
Should not have
• too many colors, graphs etc.

```html
<!DOCTYPE html>
<html lang="en">
<head>
<meta charset="utf-8">
<title>Briefly Ledger — News Papers Headlines</title>
<link rel="stylesheet" href="https://fonts.googleapis.com/css2?family=Arimo:wght@400;700&family=Open+Sans:wght@300;400;700;800&display=swap">
<style>
  :root {
    --royal: #0255a3;
    --accent-red: #ec1f27;
    --page-bg: #f8f8f8;
    --panel-bg: #e4e4e4;
    --white: #ffffff;
    --ink: #111111;
    --muted: #888888;
    --line: #dcdcdc;
    --footer-bg: #262626;
    --footer-ink: #c8c8c8;
    --photo-band: linear-gradient(160deg, #5b4a3a 0%, #3a3530 55%, #7a5a32 100%);
    --photo-sport: linear-gradient(160deg, #c9202a 0%, #8e1a1f 50%, #e9e4e0 100%);
  }
  * { box-sizing: border-box; margin: 0; padding: 0; }
  html, body { width: 1200px; height: 772px; overflow: hidden; }
  body {
    position: relative;
    background: var(--page-bg);
    font-family: "Open Sans", Arial, sans-serif;
    color: var(--ink);
  }

  /* Header */
  .site-header {
    position: absolute; left: 0; top: 0; width: 1200px; height: 61px;
    background: var(--white);
    border-bottom: 1px solid var(--line);
  }
  .brand {
    position: absolute; left: 19px; top: 14px;
    display: flex; align-items: center; gap: 14px;
    font-family: "Arimo", Arial, sans-serif; font-weight: 700;
    font-size: 21px; letter-spacing: 0.4px; color: var(--royal);
  }
  .brand-mark {
    width: 33px; height: 33px; border: 3px solid var(--royal); border-radius: 4px;
  }
  .social {
    position: absolute; left: 883px; top: 0; width: 189px; height: 61px;
    background: #f6f6f6; border-left: 1px solid var(--line);
    display: flex; align-items: center; justify-content: center; gap: 4px;
    list-style: none;
  }
  .social a {
    display: block; padding: 9px 4px;
    font-family: "Arimo", Arial, sans-serif; font-weight: 700; font-size: 10px;
    color: var(--royal); text-decoration: none;
  }
  .sign-in {
    position: absolute; left: 1072px; top: 0; width: 128px; height: 61px;
    background: var(--royal); color: var(--white);
    display: flex; align-items: center; justify-content: center;
    font-family: "Arimo", Arial, sans-serif; font-weight: 700; font-size: 13.5px;
    text-decoration: none;
  }

  /* Tabs */
  .feed { position: absolute; left: 91px; top: 129px; width: 1016px; }
  .tabs { display: flex; height: 63px; list-style: none; }
  .tab {
    flex: 1; display: flex; align-items: center; justify-content: center;
    padding-right: 22px;
    background: var(--white);
    border: 1px solid var(--line); border-left: none;
    font-family: "Arimo", Arial, sans-serif; font-weight: 700; font-size: 19.2px;
    color: var(--ink); white-space: nowrap;
  }
  .tab.is-active { background: var(--royal); color: var(--white); border-color: var(--royal); }

  .panel { position: relative; height: 450px; background: var(--panel-bg); }
  .card-track {
    position: absolute; left: 25px; top: 21px; width: 969px; height: 355px;
    overflow: hidden;
  }
  .card-row { display: flex; gap: 19px; width: 1200px; }
  .card {
    flex: 0 0 327px; height: 355px; background: var(--white);
    padding: 17px 18px 0 18px; position: relative; overflow: hidden;
  }
  .card-photo { width: 292px; height: 186px; }
  .card-photo.band { background: var(--photo-band); }
  .card-photo.sport { background: var(--photo-sport); }
  .card-title {
    margin-top: 17px; padding-left: 1px;
    font-weight: 800; font-size: 16.2px; letter-spacing: 0.3px;
    white-space: nowrap;
  }
  .card-text {
    margin-top: 6px; padding-left: 1px;
    font-weight: 300; font-size: 16.2px; line-height: 19.5px;
    color: var(--muted);
  }
  .card-meta {
    position: absolute; left: 20px; right: 19px; bottom: 19px; height: 31px;
    display: flex; align-items: center; justify-content: space-between;
  }
  .card-date { display: flex; align-items: center; gap: 13px; font-weight: 700; font-size: 13.3px; }
  .read-more {
    width: 106px; height: 31px; background: var(--royal); color: var(--white);
    display: flex; align-items: center; justify-content: center;
    font-weight: 700; font-size: 12.8px; text-decoration: none; white-space: nowrap;
  }

  .scroll-bar {
    position: absolute; left: 74px; top: 406px; width: 870px; height: 9px;
    background: var(--white);
  }
  .scroll-thumb {
    position: absolute; left: 93px; top: 0; width: 195px; height: 9px;
    background: var(--royal);
  }

  /* Footer */
  .site-footer {
    position: absolute; left: 0; top: 716px; width: 1200px; height: 56px;
    background: var(--footer-bg); color: var(--footer-ink);
    display: flex; align-items: center; justify-content: center;
    font-family: "Arimo", Arial, sans-serif; font-size: 12px;
  }
</style>
</head>
<body>
  <header class="site-header">
    <div class="brand"><span class="brand-mark"></span>BRIEFLY LEDGER</div>
    <ul class="social">
      <li><a href="#">Vexa</a></li>
      <li><a href="#">Orby</a></li>
      <li><a href="#">Nudo</a></li>
      <li><a href="#">Kiro</a></li>
      <li><a href="#">Zell</a></li>
    </ul>
    <a class="sign-in" href="#">SIGN IN</a>
  </header>

  <main class="feed">
    <ul class="tabs">
      <li class="tab is-active">NEWS PAPERS HEADLINES</li>
      <li class="tab">EVENTS</li>
      <li class="tab">DAILY BRIEFING</li>
    </ul>

    <section class="panel">
      <div class="card-track">
        <div class="card-row">
          <article class="card">
            <div class="card-photo band" role="img" aria-label="Photo of a rock band rehearsing in a cluttered practice room"></div>
            <h3 class="card-title">LOREM IPSUM DOLOR SIT AMET.</h3>
            <p class="card-text">Duis autem vel eum iriure dolor in hendrerit invulputate velit.</p>
            <div class="card-meta">
              <span class="card-date">
                <svg width="18" height="18" viewBox="0 0 18 18" aria-hidden="true"><rect x="1.5" y="3" width="15" height="13.5" fill="none" stroke="#ec1f27" stroke-width="1.5"/><line x1="1.5" y1="6.5" x2="16.5" y2="6.5" stroke="#ec1f27" stroke-width="1.5"/><line x1="5" y1="1" x2="5" y2="4.5" stroke="#ec1f27" stroke-width="1.5"/><line x1="13" y1="1" x2="13" y2="4.5" stroke="#ec1f27" stroke-width="1.5"/><g fill="#ec1f27"><rect x="4" y="9" width="2" height="2"/><rect x="8" y="9" width="2" height="2"/><rect x="12" y="9" width="2" height="2"/><rect x="4" y="12.5" width="2" height="2"/><rect x="8" y="12.5" width="2" height="2"/><rect x="12" y="12.5" width="2" height="2"/></g></svg>
                Jan 05, 2016
              </span>
              <a class="read-more" href="#">Read More</a>
            </div>
          </article>
          <article class="card">
            <div class="card-photo sport" role="img" aria-label="Photo of a football player in a red jersey and helmet celebrating"></div>
            <h3 class="card-title">LOREM IPSUM DOLOR SIT AMET.</h3>
            <p class="card-text">Duis autem vel eum iriure dolor in hendrerit invulputate velit.</p>
            <div class="card-meta">
              <span class="card-date">
                <svg width="18" height="18" viewBox="0 0 18 18" aria-hidden="true"><rect x="1.5" y="3" width="15" height="13.5" fill="none" stroke="#ec1f27" stroke-width="1.5"/><line x1="1.5" y1="6.5" x2="16.5" y2="6.5" stroke="#ec1f27" stroke-width="1.5"/><line x1="5" y1="1" x2="5" y2="4.5" stroke="#ec1f27" stroke-width="1.5"/><line x1="13" y1="1" x2="13" y2="4.5" stroke="#ec1f27" stroke-width="1.5"/><g fill="#ec1f27"><rect x="4" y="9" width="2" height="2"/><rect x="8" y="9" width="2" height="2"/><rect x="12" y="9" width="2" height="2"/><rect x="4" y="12.5" width="2" height="2"/><rect x="8" y="12.5" width="2" height="2"/><rect x="12" y="12.5" width="2" height="2"/></g></svg>
                Jan 05, 2016
              </span>
              <a class="read-more" href="#">Read More</a>
            </div>
          </article>
          <article class="card">
            <div class="card-photo band" role="img" aria-label="Photo of a rock band rehearsing in a cluttered practice room"></div>
            <h3 class="card-title">LOREM IPSUM DOLOR SIT AMET.</h3>
            <p class="card-text">Duis autem vel eum iriure dolor in hendrerit invulputate velit.</p>
            <div class="card-meta">
              <span class="card-date">
                <svg width="18" height="18" viewBox="0 0 18 18" aria-hidden="true"><rect x="1.5" y="3" width="15" height="13.5" fill="none" stroke="#ec1f27" stroke-width="1.5"/><line x1="1.5" y1="6.5" x2="16.5" y2="6.5" stroke="#ec1f27" stroke-width="1.5"/><line x1="5" y1="1" x2="5" y2="4.5" stroke="#ec1f27" stroke-width="1.5"/><line x1="13" y1="1" x2="13" y2="4.5" stroke="#ec1f27" stroke-width="1.5"/><g fill="#ec1f27"><rect x="4" y="9" width="2" height="2"/><rect x="8" y="9" width="2" height="2"/><rect x="12" y="9" width="2" height="2"/><rect x="4" y="12.5" width="2" height="2"/><rect x="8" y="12.5" width="2" height="2"/><rect x="12" y="12.5" width="2" height="2"/></g></svg>
                Jan 05, 2016
              </span>
              <a class="read-more" href="#">Read More</a>
            </div>
          </article>
        </div>
      </div>
      <div class="scroll-bar"><div class="scroll-thumb"></div></div>
    </section>
  </main>

  <footer class="site-footer">COPYRIGHT © 2016 BRIEFLYLEDGER.</footer>
</body>
</html>
```